Vorelan.com Personal Trainer/Fitness Website

I want a website to market my personal training/Outdoor Bootcamp Class services, as well as to ditribute nutrivex. I need a logo as well I included an address for the Harbor Gales 1975 logo. I'd like Vorelan in place of Harbor Gales, and in Black and white, just different enough so I can't get sued by the PBL.
https://www.pictofind.example/imgres?imgurl=http%3A%2F%2Fwww.darnell-quibury.example%2Fwp-content%2Fuploads%2F2014%2F01%2Fgales_logo4.jpg&imgrefurl=http%3A%2F%2Fwww.darnell-quibury.example%2Fpbl-logo-redesigns-harbor-gales%2F&docid=_qkwzR7TBAgXpL&tbnid=m4tpU8KdOXjnRP%3A&w=600&h=450&client=ms-android-carrier&bih=512&biw=360&ved=0ahUKEwiRtpgyp9HMAhUTwGMKHRPMBWMQMwg6KBQwFA&iact=mrc&uact=8.
It should be about 5 pages 1. home 2. about 3. Services 4. Blog/Videos and programs 5. Contact.
http://www.dorvinfitness.example.uk/ is a website I like the style of.

Target Market(s)

Seattle area

Industry/Entity Type

Fitness

Coding

Coded - Design and coding required

Number of Pages Required

4 page

Font styles to use
Serif
Sans Serif

Requirements
Must have
• A minimal look
Nice to have
• A logo similar to the 1975 Harbor Galewinds Logo, with a Small Milo Brandt ripping his shirt open(with a picture of the logo on his shirt, picture within picture) to turn into Ironjaw in the center. Skyline is black, Background and small figure white(with black logo on shirt)

```html
<!DOCTYPE html>
<html lang="en">
<head>
<meta charset="utf-8">
<title>Vorelan – Personal Training &amp; Outdoor Bootcamp</title>
<link rel="stylesheet" href="https://fonts.googleapis.com/css2?family=Raleway:wght@400;600;700;800&family=Open+Sans:wght@400;600&display=swap">
<style>
:root{
  --green:#7cb22b;
  --green-dark:#5f8f1c;
  --yellow:#f6b40e;
  --ink:#333333;
  --muted:#6f6f6f;
  --line:#e3e3e3;
  --band:#eeeeee;
  --footer:#2a2a2a;
  --footer-text:#cfcfcf;
  --white:#ffffff;
}
*{box-sizing:border-box;margin:0;padding:0}
html,body{width:1200px;height:2480px;overflow:hidden;background:var(--white)}
body{font-family:"Open Sans",Arial,sans-serif;color:var(--ink);position:relative}
h1,h2,h3,.nav,.brand{font-family:"Raleway",Arial,sans-serif}
.page{position:relative;width:1200px;height:2480px}

/* header */
.site-header{position:absolute;top:0;left:0;width:1200px;height:112px;background:var(--white)}
.brand{position:absolute;left:128px;top:22px;display:flex;align-items:center;gap:14px;font-weight:800;font-size:34px;color:var(--green);letter-spacing:1px}
.brand-dot{width:62px;height:62px;border-radius:50%;background:var(--green)}
.contact-bar{position:absolute;right:132px;top:8px;font-size:13px;color:var(--muted);display:flex;gap:22px}
.contact-bar span{display:flex;align-items:center;gap:6px}
.nav{position:absolute;right:132px;top:56px;display:flex;gap:6px;font-size:15px;font-weight:600}
.nav a{color:var(--ink);text-decoration:none;padding:10px 16px}
.nav a.active{border:1px solid var(--line);border-bottom:3px solid var(--green)}

/* hero */
.hero{position:absolute;top:112px;left:0;width:1200px;height:490px;background:linear-gradient(180deg,#8fae6a 0%,#5f8a3b 45%,#3f6424 100%)}
.hero-text{position:absolute;left:132px;top:382px;color:var(--white)}
.hero-text h1{font-size:44px;font-weight:800;letter-spacing:1px}
.hero-text h1 em{font-style:normal;color:var(--yellow)}
.hero-text p{font-size:19px;margin-top:6px}

/* welcome */
.welcome{position:absolute;top:602px;left:0;width:1200px;height:378px}
.welcome h2{position:absolute;left:132px;top:30px;font-size:36px;font-weight:600}
.welcome .copy{position:absolute;left:132px;top:100px;width:640px;font-size:14px;line-height:24px;color:var(--muted)}
.welcome .copy p+p{margin-top:4px}
.btn{display:inline-block;background:#d9d9d9;color:var(--ink);font-size:13px;padding:8px 20px;border-radius:2px}
.welcome .btn{position:absolute;left:132px;top:306px}
.trainer-photo{position:absolute;left:820px;top:20px;width:260px;height:358px;background:linear-gradient(180deg,#f1f1f1,#c9d6de)}

/* services */
.services{position:absolute;top:980px;left:0;width:1200px;height:440px;background:linear-gradient(180deg,#d8d8d8,#bdbdbd)}
.section-title{font-size:38px;font-weight:600;text-align:center}
.section-title span{color:var(--green)}
.services .section-title{position:absolute;top:46px;width:1200px}
.services .lead{position:absolute;top:110px;left:300px;width:600px;text-align:center;font-size:14px;line-height:22px;color:#555}
.service-card{position:absolute;top:196px;width:288px}
.service-card .media{height:182px}
.service-card .label{height:40px;background:var(--yellow);color:var(--white);font-weight:600;font-size:16px;text-align:center;line-height:40px}

/* programs */
.programs{position:absolute;top:1470px;left:0;width:1200px;height:320px}
.programs h2{position:absolute;left:132px;top:18px;font-size:34px;font-weight:600}
.programs h2 span{color:var(--green)}
.programs .thumb{position:absolute;left:132px;top:100px;width:206px;height:190px;background:linear-gradient(160deg,#a8c48a,#6f9257)}
.program-list{position:absolute;left:360px;top:96px;list-style:none;font-size:14px;line-height:25px;color:var(--muted)}
.program-list li{display:flex;align-items:center;gap:10px}
.program-list li::before{content:"";width:7px;height:7px;border-radius:50%;background:var(--green)}
.programs .btn{position:absolute;left:360px;top:254px}
.video{position:absolute;left:722px;top:38px;width:350px;height:214px;background:linear-gradient(160deg,#9bbd7a,#587a3c)}
.video svg{position:absolute;left:139px;top:71px}
.video-caption{position:absolute;left:722px;top:262px;width:350px;text-align:center;font-size:19px;color:var(--ink);text-decoration:underline}

/* testimonial */
.testimonial{position:absolute;top:1808px;left:132px;width:940px;height:172px;background:var(--band)}
.testimonial .arrow{position:absolute;top:70px}
.avatar{position:absolute;left:96px;top:36px;width:100px;height:100px;border-radius:50%;background:linear-gradient(160deg,#c9a37f,#7d5a42)}
.testimonial blockquote{position:absolute;left:220px;top:34px;width:620px;font-size:14px;line-height:22px;color:var(--muted)}
.testimonial cite{display:block;margin-top:6px;font-style:normal;color:var(--green);font-weight:600}

/* blog */
.blog{position:absolute;top:2000px;left:0;width:1200px;height:300px}
.blog .section-title{position:absolute;top:0;width:1200px}
.post{position:absolute;top:72px;width:460px;height:170px}
.post .media{position:absolute;left:0;top:0;width:150px;height:168px}
.post .body{position:absolute;left:178px;top:0;width:280px}
.post h3{font-size:17px;font-weight:700;line-height:22px}
.post .meta{font-size:11px;color:#999;margin:4px 0 8px}
.post p{font-size:13px;line-height:20px;color:var(--muted)}
.post .more{font-size:13px;color:var(--ink);margin-top:2px}

/* footer */
.site-footer{position:absolute;top:2312px;left:0;width:1200px;height:168px;background:var(--footer);color:var(--footer-text);text-align:center}
.social{position:absolute;top:30px;left:0;width:1200px;display:flex;justify-content:center;gap:10px}
.social i{width:30px;height:30px;display:block;border-radius:3px}
.footer-nav{position:absolute;top:84px;width:1200px;font-family:"Raleway",Arial,sans-serif;font-size:14px}
.footer-nav a{color:var(--footer-text);text-decoration:none;margin:0 10px}
.copyright{position:absolute;top:124px;width:1200px;font-size:13px;color:#9a9a9a}
</style>
</head>
<body>
<div class="page">

<header class="site-header">
  <div class="brand"><span class="brand-dot"></span>VORELAN</div>
  <div class="contact-bar">
    <span><svg width="12" height="12" viewBox="0 0 24 24"><path fill="#7cb22b" d="M6.6 10.8a15 15 0 0 0 6.6 6.6l2.2-2.2c.3-.3.7-.4 1-.2 1.1.4 2.3.6 3.6.6.6 0 1 .4 1 1V20c0 .6-.4 1-1 1A17 17 0 0 1 3 4c0-.6.4-1 1-1h3.5c.6 0 1 .4 1 1 0 1.3.2 2.5.6 3.6.1.3 0 .7-.2 1z"/></svg>(425) 555 0142</span>
    <span><svg width="13" height="10" viewBox="0 0 26 20"><rect x="1" y="1" width="24" height="18" fill="none" stroke="#7cb22b" stroke-width="2"/><path d="M1 1l12 10L25 1" fill="none" stroke="#7cb22b" stroke-width="2"/></svg>info@vorelanfit.example</span>
  </div>
  <nav class="nav">
    <a class="active">Home</a><a>About Us</a><a>Services</a><a>Blog</a><a>Videos and Programs</a><a>Contact Us</a>
  </nav>
</header>

<section class="hero" role="img" aria-label="Group of people exercising outdoors on a park lawn, arms raised">
  <div class="hero-text">
    <h1>GET <em>FIT!</em> GET <em>STRONG!</em> GET <em>OUTDOORS!</em></h1>
    <p>Workouts custom tailored to you</p>
  </div>
</section>

<section class="welcome">
  <h2>Welcome to VORELAN</h2>
  <div class="copy">
    <p>Lorem Ipsum is simply dummy text of the printing and typesetting industry. Lorem Ipsum has been the industry's standard dummy text ever since the 1500s, when an unknown printer took a galley of type and scrambled it to make a type specimen book. It has survived not only five centuries, but also the leap into electronic typesetting, remaining essentially unchanged.</p>
    <p>It was popularised in the 1960s with the release of Letraset sheets containing Lorem Ipsum passages, and more recently with desktop publishing software like Aldus PageMaker including versions of Lorem Ipsum.</p>
  </div>
  <span class="btn">Read More</span>
  <div class="trainer-photo" role="img" aria-label="Smiling personal trainer in a blue sleeveless shirt, arms crossed"></div>
</section>

<section class="services">
  <h2 class="section-title">Our <span>Services</span></h2>
  <p class="lead">Lorem Ipsum is simply dummy text of the printing and typesetting industry. Lorem Ipsum has been the industry's standard dummy text ever since, when an unknown printer took a galley of type.</p>
  <div class="service-card" style="left:132px"><div class="media" role="img" aria-label="Trainer coaching a client on a mat" style="background:linear-gradient(160deg,#d7b99a,#8c6d52)"></div><div class="label">Personal Training</div></div>
  <div class="service-card" style="left:456px"><div class="media" role="img" aria-label="Outdoor bootcamp group training on grass" style="background:linear-gradient(160deg,#a9c98a,#5d8a3d)"></div><div class="label">Outdoor Bootcamp</div></div>
  <div class="service-card" style="left:780px"><div class="media" role="img" aria-label="Small group doing exercises in a park" style="background:linear-gradient(160deg,#b5cf95,#6c9448)"></div><div class="label">Small Group Training</div></div>
</section>

<section class="programs">
  <h2>Our Workout <span>Programs</span></h2>
  <div class="thumb" role="img" aria-label="People stretching outdoors"></div>
  <ul class="program-list">
    <li>Donec gravida turpis vitae semper gravida</li>
    <li>Fusce cursus nulla at tristique ullamcorper</li>
    <li>Sed mattis purus consequat imperdiet.</li>
    <li>Morbi id nisl quis nisl in rhoncus consectetur.</li>
    <li>Proin iaculis nibh vel quam tempor lobortis</li>
  </ul>
  <span class="btn">View Workout Programs</span>
  <div class="video" role="img" aria-label="Video still of an outdoor workout session">
    <svg width="72" height="72" viewBox="0 0 72 72"><circle cx="36" cy="36" r="34" fill="#ffffff" opacity=".9"/><path d="M29 22l22 14-22 14z" fill="#5f8f1c"/></svg>
  </div>
  <div class="video-caption">Click to Watch our Video</div>
</section>

<section class="testimonial">
  <svg class="arrow" style="left:26px" width="16" height="30" viewBox="0 0 16 30"><path d="M14 2L2 15l12 13" fill="none" stroke="#b5b5b5" stroke-width="3"/></svg>
  <div class="avatar" role="img" aria-label="Portrait of a client"></div>
  <blockquote>" Lorem Ipsum is simply dummy text of the printing and typesetting industry. Lorem Ipsum has been the industry's standard dummy text ever since an unknown printer took a galley of type and it but also the leap into electronic typesetting, remaining essentially unchanged."
    <cite>Renata Holloway</cite></blockquote>
  <svg class="arrow" style="right:26px" width="16" height="30" viewBox="0 0 16 30"><path d="M2 2l12 13L2 28" fill="none" stroke="#b5b5b5" stroke-width="3"/></svg>
</section>

<section class="blog">
  <h2 class="section-title">Our Latest <span>Blog</span></h2>
  <article class="post" style="left:132px">
    <div class="media" role="img" aria-label="Member training outdoors" style="background:linear-gradient(160deg,#b0cc8f,#66904a)"></div>
    <div class="body">
      <h3>Member Of the Month</h3>
      <div class="meta">Posted on June 12, 2016</div>
      <p>It is a long established fact that a reader will be distracted by the readable content of a page when looking at its layout.</p>
      <div class="more">Read More »</div>
    </div>
  </article>
  <article class="post" style="left:620px">
    <div class="media" role="img" aria-label="Group doing a park workout" style="background:linear-gradient(160deg,#a6c58b,#5b8440)"></div>
    <div class="body">
      <h3>What are you gonna do with all that fitness?</h3>
      <div class="meta">Posted on June 08, 2016</div>
      <p>It is a long established fact that a reader will be distracted by the readable content of a page.</p>
      <div class="more">Read More »</div>
    </div>
  </article>
</section>

<footer class="site-footer">
  <div class="social"><i style="background:#3b5a99"></i><i style="background:#2aa3ef"></i><i style="background:#d23e2b"></i><i style="background:#e05a1f"></i></div>
  <div class="footer-nav"><a>Home</a>|<a>About Us</a>|<a>Services</a>|<a>Blog</a>|<a>Videos and Programs</a>|<a>Contact Us</a></div>
  <div class="copyright">© 2016. VORELAN. All Right Reserved</div>
</footer>

</div>
</body>
</html>
```